Business cards to launch an education platform

Hi,
I am looking at having new business cards designed.
I am a startup, developing a web platform for schools and university, the education world. It's an online assessment system.
I would like a card that looks classy, and that is using the colors and the font of my logo.

I have attached:
1) my logo
2) A business card that I have designed quickly so you can have all the information required in the card, but I really don't like it.
3) The font that I am using (Lato Regular) to design my web platform
4) Some screenshots of my web platform so you can have a look at the style that I have.

Target Market(s)

Major market: Education system: Schools and university
Minor markets: Business in general

Industry/Entity Type

Business

Contact Information for Business Card

Clara Fenwick
Director

M: 0437 518 902
E: clara.fenwick@amberLoomSystems.com.au

Requirements
Must have
• The colors of my logo

```html
<!DOCTYPE html>
<html lang="en">
<head>
<meta charset="utf-8">
<title>Amber Loom Systems – Business Cards</title>
<link href="https://fonts.googleapis.com/css2?family=Lato:wght@400;700&family=Oswald:wght@600&display=swap" rel="stylesheet">
<style>
  :root {
    --backdrop: #7b7d7f;
    --card: #ffffff;
    --brand-deep: #1a5f9e;
    --brand-bright: #1e8fd6;
    --ink-muted: #2f4f6e;
    --icon-bg: #1b7fc7;
  }
  * { margin: 0; padding: 0; box-sizing: border-box; }
  html, body { width: 1200px; height: 902px; overflow: hidden; }
  body {
    background: var(--backdrop);
    font-family: "Lato", sans-serif;
    position: relative;
  }
  .card {
    position: absolute;
    width: 500px;
    height: 290px;
    background: var(--card);
    border-radius: 24px;
    box-shadow: 0 6px 18px rgba(0,0,0,0.25);
  }
  .card--front { left: 70px; top: 306px; }
  .card--back { left: 630px; top: 306px; }

  .brand {
    position: absolute;
    display: flex;
    align-items: center;
  }
  .brand__mark {
    background: var(--brand-deep);
    flex: none;
  }
  .brand__name {
    color: var(--brand-deep);
    font-weight: 400;
    letter-spacing: 2px;
    line-height: 1.1;
    text-transform: uppercase;
  }
  .card--front .brand { left: 110px; top: 110px; }
  .card--front .brand__mark { width: 64px; height: 64px; margin-right: 16px; }
  .card--front .brand__name { font-size: 28px; }

  .card--back .brand { right: 38px; top: 38px; }
  .card--back .brand__mark { width: 40px; height: 40px; margin-right: 10px; }
  .card--back .brand__name { font-size: 17px; }

  .person {
    position: absolute;
    left: 36px;
    top: 140px;
  }
  .person__name {
    font-family: "Oswald", sans-serif;
    font-weight: 600;
    font-size: 30px;
    color: var(--brand-bright);
    text-transform: uppercase;
    line-height: 1;
  }
  .person__title {
    font-size: 9px;
    letter-spacing: 1.5px;
    color: var(--ink-muted);
    text-transform: uppercase;
    margin-top: 4px;
  }
  .contacts {
    list-style: none;
    margin-top: 12px;
  }
  .contacts__item {
    display: flex;
    align-items: center;
    font-size: 11.5px;
    color: var(--ink-muted);
    height: 17px;
    margin-bottom: 4px;
    white-space: nowrap;
  }
  .contacts__icon {
    width: 14px;
    height: 14px;
    border-radius: 3px;
    background: var(--icon-bg);
    margin-right: 9px;
    flex: none;
    display: flex;
    align-items: center;
    justify-content: center;
  }
  .contacts__icon svg { width: 10px; height: 10px; }
</style>
</head>
<body>
  <section class="card card--front" aria-label="Card front">
    <div class="brand">
      <span class="brand__mark"></span>
      <span class="brand__name">Amber Loom<br>Systems</span>
    </div>
  </section>

  <section class="card card--back" aria-label="Card back">
    <div class="brand">
      <span class="brand__mark"></span>
      <span class="brand__name">Amber Loom<br>Systems</span>
    </div>

    <div class="person">
      <p class="person__name">Clara Fenwick</p>
      <p class="person__title">Director</p>
      <ul class="contacts">
        <li class="contacts__item">
          <span class="contacts__icon"><svg viewBox="0 0 10 10"><path d="M2 1.5 L3.6 1.2 L4.3 3 L3.3 3.8 Q4.2 5.8 6.2 6.7 L7 5.7 L8.8 6.4 L8.5 8 Q4.5 8.5 1.5 4.5 Q1.3 2.8 2 1.5 Z" fill="#fff"/></svg></span>
          M: 0437 518 902
        </li>
        <li class="contacts__item">
          <span class="contacts__icon"><svg viewBox="0 0 10 10"><rect x="1.2" y="2.4" width="7.6" height="5.2" fill="none" stroke="#fff" stroke-width="0.9"/><path d="M1.2 2.6 L5 5.5 L8.8 2.6" fill="none" stroke="#fff" stroke-width="0.9"/></svg></span>
          E: clara.fenwick@amberLoomSystems.com.au
        </li>
        <li class="contacts__item">
          <span class="contacts__icon"><svg viewBox="0 0 10 10"><circle cx="5" cy="5" r="3.7" fill="none" stroke="#fff" stroke-width="0.9"/><ellipse cx="5" cy="5" rx="1.6" ry="3.7" fill="none" stroke="#fff" stroke-width="0.8"/><path d="M1.3 5 H8.7" stroke="#fff" stroke-width="0.8"/></svg></span>
          www.amberloomsystems.com.au
        </li>
      </ul>
    </div>
  </section>
</body>
</html>
```